New website for concierge mobile medical service

new website for business:
WEBSITE REQUEST LIST:
Luxury product look.
Professional. Clean & simple, NO stock people photos. Graphics OK.
Black and white text.

```html
<!DOCTYPE html>
<html lang="en">
<head>
<meta charset="utf-8">
<title>Nimbus Health – Meet The Doctors</title>
<link rel="stylesheet" href="https://fonts.googleapis.com/css2?family=Lato:wght@400;700;900&display=swap">
<style>
:root{
  --navy:#173a4d;
  --ink:#2b2b2b;
  --purple:#7167b6;
  --blue:#4a6db5;
  --card:#f2f2f2;
  --teal:#1a93b0;
  --teal-light:#9ad7df;
  --footer:#262626;
  --white:#ffffff;
}
*{margin:0;padding:0;box-sizing:border-box}
html,body{width:1015px;height:1200px;overflow:hidden;background:var(--white)}
body{position:relative;font-family:"Lato",sans-serif;color:var(--ink)}
.abs{position:absolute}

/* header */
.site-header{position:absolute;left:0;top:0;width:1015px;height:91px;background:var(--white);z-index:2}
.brand{position:absolute;left:133px;top:16px;width:106px;height:106px;border-radius:50%;background:var(--white);display:flex;align-items:center;justify-content:center;z-index:3}
.brand-mark{width:88px;height:88px;border-radius:50%;background:var(--navy);display:flex;align-items:center;justify-content:center;color:var(--white);font-weight:700;font-size:14px;text-align:center;line-height:1.1}
.phone{position:absolute;left:750px;top:14px;display:flex;align-items:center;gap:11px}
.phone-icon{width:27px;height:27px;background:var(--purple);display:flex;align-items:center;justify-content:center}
.phone-number{color:var(--purple);font-size:16px;font-weight:700}
.main-nav{position:absolute;top:63px;left:0;width:1015px;font-size:10.5px;font-weight:700;color:#1e1e1e}
.main-nav a{position:absolute;white-space:nowrap;text-decoration:none;color:inherit}
.main-nav a.active{color:var(--navy)}
.nav-indicator{position:absolute;left:387px;top:86px;width:79px;height:5px;background:var(--navy)}

/* hero */
.hero{position:absolute;left:0;top:91px;width:1015px;height:224px;background:linear-gradient(100deg,#02080d 0%,#031d30 40%,#0a3b5e 75%,#0e4f78 100%)}
.hero-title{position:absolute;left:122px;top:85px;color:var(--white);font-size:38px;font-weight:900;letter-spacing:.2px}
.hero-emblem{position:absolute;left:732px;top:25px;width:174px;height:174px;border-radius:50%;border:3px solid #7fd3e6;background:radial-gradient(circle,#0d4a70 0%,#0b3a59 100%)}

/* intro */
.intro{position:absolute;left:120px;top:342px;width:775px;text-align:center;font-size:11.6px;line-height:23px;color:#333}

/* team */
.card{position:absolute;width:177px;height:110px;background:var(--card)}
.avatar{position:absolute;width:108px;height:108px;border-radius:50%;background:var(--white)}
.avatar.selected{border:3px solid #9a8cc8}
.avatar svg{position:absolute;left:50%;top:50%;transform:translate(-50%,-50%)}
.card-name{position:absolute;width:177px;text-align:center;font-size:16px;font-weight:700;color:var(--blue)}
.bio{position:absolute;left:248px;top:598px;width:320px;height:179px;background:linear-gradient(180deg,#5470b8 0%,#9a8cc5 100%);box-shadow:0 2px 6px rgba(0,0,0,.18);color:var(--white);text-align:center;padding:18px 18px 0}
.bio::before{content:"";position:absolute;left:153px;top:-8px;border-left:8px solid transparent;border-right:8px solid transparent;border-bottom:8px solid #5470b8}
.bio-name{font-size:17.5px;font-weight:700;margin-bottom:5px}
.bio-text{font-size:11.6px;line-height:20.3px}

/* subscribe */
.subscribe{position:absolute;left:0;top:872px;width:1015px;height:213px;background:linear-gradient(120deg,#1a93b0 0%,#178aa8 50%,#1f9ab8 100%)}
.subscribe-title{position:absolute;top:34px;width:1015px;text-align:center;color:var(--white);font-size:27px;font-weight:700}
.field{position:absolute;top:88px;width:269px;height:36px;background:var(--white);font-size:10.5px;color:#333;padding:12px 13px}
.subscribe-btn{position:absolute;left:233px;top:132px;width:549px;height:38px;background:var(--teal-light);color:var(--white);font-size:13.5px;font-weight:700;text-align:center;line-height:38px}

/* footer */
.site-footer{position:absolute;left:0;top:1085px;width:1015px;height:115px;background:var(--footer);color:var(--white)}
.footer-nav a{position:absolute;top:21px;font-size:10.5px;font-weight:700;color:var(--white);text-decoration:none;white-space:nowrap}
.copyright{position:absolute;top:49px;width:1015px;text-align:center;font-size:9.6px}
.social{position:absolute;top:76px;left:444px;display:flex;gap:15px}
.social span{width:14px;height:14px;border-radius:50%;background:var(--white)}
</style>
</head>
<body>

<header class="site-header">
  <div class="brand"><div class="brand-mark">Nimbus<br>Health</div></div>
  <div class="phone">
    <div class="phone-icon">
      <svg width="14" height="14" viewBox="0 0 24 24"><path fill="#fff" d="M6.6 10.8a15.1 15.1 0 0 0 6.6 6.6l2.2-2.2c.3-.3.7-.4 1-.2 1.1.4 2.3.6 3.6.6.6 0 1 .4 1 1V20c0 .6-.4 1-1 1A17 17 0 0 1 3 4c0-.6.4-1 1-1h3.5c.6 0 1 .4 1 1 0 1.3.2 2.5.6 3.6.1.3 0 .7-.2 1z"/></svg>
    </div>
    <span class="phone-number">555-010-0142</span>
  </div>
  <nav class="main-nav">
    <a style="left:334px">HOME</a>
    <a class="active" style="left:401px">ABOUT US</a>
    <a style="left:489px">WHY NIMBUS?</a>
    <a style="left:588px">SERVICE AREA</a>
    <a style="left:698px">OTHER</a>
    <a style="left:769px">FAQ</a>
    <a style="left:824px">CONTACT US</a>
  </nav>
</header>
<div class="nav-indicator"></div>

<section class="hero" role="img" aria-label="Dark blue medical network background">
  <h1 class="hero-title">Meet The Doctors</h1>
  <div class="hero-emblem" role="img" aria-label="Emblem of a car with a medical staff symbol"></div>
</section>

<p class="intro">We are Board Certified physicians. Dr. Leo Varga , Dr. Max Hollis , along with Ian ____, PA, Nora ______PA, and Owen Pratt, PA have together treated over 300,000 patients. Each provider has extensive experience evaluating and treating acute illnesses and injuries in the ER and private practice and are trained as well in primary care. Not only that, we are fun to be around and we love taking care of people. We’ll always follow up after we’ve treated you, to see how you’re doing and to make sure you are recovering well.</p>

<!-- row one -->
<div class="card" style="left:320px;top:522px"></div>
<div class="card" style="left:518px;top:522px"></div>
<div class="card-name" style="left:518px;top:590px">Dr. Max</div>
<!-- row two -->
<div class="card" style="left:221px;top:708px"></div>
<div class="card" style="left:420px;top:708px"></div>
<div class="card" style="left:618px;top:708px"></div>
<div class="card-name" style="left:221px;top:778px">Owen PA</div>
<div class="card-name" style="left:420px;top:778px">Ian PA</div>
<div class="card-name" style="left:618px;top:778px">Nora PA</div>

<div class="avatar selected" style="left:355px;top:468px">
  <svg width="40" height="44" viewBox="0 0 40 44"><circle cx="20" cy="11" r="11" fill="#173a4d"/><path d="M0 44v-10c0-6 5-10 10-10h20c5 0 10 4 10 10v10z" fill="#173a4d"/></svg>
</div>
<div class="avatar" style="left:553px;top:468px">
  <svg width="40" height="44" viewBox="0 0 40 44"><circle cx="20" cy="11" r="11" fill="#173a4d"/><path d="M0 44v-10c0-6 5-10 10-10h20c5 0 10 4 10 10v10z" fill="#173a4d"/></svg>
</div>
<div class="avatar" style="left:652px;top:654px">
  <svg width="40" height="44" viewBox="0 0 40 44"><circle cx="20" cy="11" r="11" fill="#173a4d"/><path d="M0 44v-10c0-6 5-10 10-10h20c5 0 10 4 10 10v10z" fill="#173a4d"/></svg>
</div>

<div class="bio">
  <div class="bio-name">Dr. Leo Varga</div>
  <p class="bio-text">Dr. Leo is an experienced and accomplished physician who has treated over 80,000 patients in primary care, acute care and emergency care. Dr. Leo is passionate about patient satisfaction which he achieves by delivering personalized care to&nbsp; each of this patients.</p>
</div>

<section class="subscribe" role="img" aria-label="Teal background with faint medical icons">
  <h2 class="subscribe-title">Subscribe</h2>
  <div class="field" style="left:233px">Enter Name</div>
  <div class="field" style="left:513px">Enter Email Address</div>
  <div class="subscribe-btn">SUBSCRIBE NOW</div>
</section>

<footer class="site-footer">
  <nav class="footer-nav">
    <a style="left:255px">HOME</a>
    <a style="left:322px">ABOUT US</a>
    <a style="left:411px">WHY NIMBUS?</a>
    <a style="left:510px">SERVICE AREA</a>
    <a style="left:620px">OTHER</a>
    <a style="left:690px">CONTACT US</a>
  </nav>
  <p class="copyright">Copyright © 2019.&nbsp; Company Name&nbsp; All Rights Reserved</p>
  <div class="social" aria-label="Social links"><span></span><span></span><span></span><span></span><span></span></div>
</footer>

</body>
</html>
```